Business card design needed to incorporate existing logo

We need a business card for a new modern Accounting & Business Solutions company call TelmaNord Partners.com.au servicing all of Australia.
My tagline is Steady Ledger Answers... that deliver.

We specialise in Cloud Accounting and this is our primary focus. We also provide tax representation, debt recovery, computer, tablet and smart phone sales.

I would like a design that uses my corporate, trustworthy colours of blue/white, black/grey however am open to suggestion. I have attached my logo to go on the card somewhere,of which you will see the colour scheme.

I am after a card that STANDS OUT, somewhere between it not being too busy and not being a baron waste of space.

A 'cloud' incorporated in the design may work well, up to your artistic judgement. I know what I like when I see it; it is harder to put into words!

Excited to see your ideas!
I have added my logo predominately (blue/white) and for additional opportunity have added my reverse logo (darker one). I have used the blue/white on my website and letterhead. I will be using both on my vehicle signage.

Target Market(s)

Tradesmen and small-medium businesses of all descriptions Australia-wide

Industry/Entity Type

Debt

Contact Information for Business Card

Doug Hallett
Principal (optional)
TelmaNord Partners.com.au
Steady Ledger Answers... that deliver

P: 1800 493 518
M: 0412 658 071 (optional)
W: www.telmanordpartners.com.au
E: admin@telmanordpartners.com.au

Logo Text

Steady Ledger Answers... that deliver!

Logo styles of interest
Wordmark Logo
Requirements
Must have
• Must look professional and of high quality not cheap.

My logo and my tagline 'Steady Ledger Answers... that deliver'.

I have my colourscheme in mind as per my attached logo, however am open to suggestion. I want to see what you can create that I would not have thought of.

Modern, innovative.
Something I won't look at and think, 'I could have done that myself'.

Must be able to be printed on Prinvo 300gm premium cards and the artwork provided to me.
Nice to have
• Title of Principal is optional depending on space and judement call of look/fee.
M: (mobile) number is also optional as above.

Somthing cloud related given the Cloud Accounting aspect may be relevant. I leave it to your artistic design and judgement.
Should not have
• Must not look cheap.

```html
<!DOCTYPE html>
<html lang="en">
<head>
<meta charset="utf-8">
<title>TelmaNord Partners – Business Card</title>
<link href="https://fonts.googleapis.com/css2?family=Didact+Gothic&family=Montserrat:wght@700&display=swap" rel="stylesheet">
<style>
  :root {
    --navy: #1a2559;
    --navy-deep: #141d4a;
    --sky: #2b8fd8;
    --sky-soft: #7bbbe8;
    --white: #ffffff;
    --paper: #f6f6f7;
    --paper-shade: #e4e4e7;
    --ink-grey: #3a3a40;
    --backdrop: #d6d6d8;
  }
  * { box-sizing: border-box; margin: 0; padding: 0; }
  html, body {
    width: 1200px; height: 1200px; overflow: hidden;
    background: var(--backdrop);
  }
  .canvas {
    width: 1200px; height: 1200px;
    display: flex; flex-direction: column; align-items: center; justify-content: center;
    gap: 50px;
  }
  .card {
    position: relative;
    width: 860px; height: 525px;
    overflow: hidden;
    box-shadow: 0 6px 18px rgba(0,0,0,0.18);
  }

  /* Reverse side */
  .card--back { background: var(--white); }
  .back-band {
    position: absolute; left: 0; right: 0; top: 125px; height: 160px;
    background: var(--navy);
    display: flex; align-items: center; justify-content: center;
  }
  .back-wordmark {
    font-family: "Didact Gothic", sans-serif;
    font-size: 46px; letter-spacing: 3px;
    color: var(--sky-soft);
  }

  /* Front side */
  .card--front {
    display: flex;
    background: linear-gradient(135deg, var(--paper-shade) 0%, var(--paper) 55%, var(--white) 100%);
  }
  .brand-panel {
    width: 390px; height: 100%;
    background: linear-gradient(90deg, var(--navy-deep), var(--navy));
    position: relative;
  }
  .brand-mark {
    position: absolute; left: 100px; top: 70px;
    width: 190px; height: 190px;
  }
  .brand-name {
    position: absolute; left: 30px; top: 290px;
    font-family: "Didact Gothic", sans-serif;
    font-size: 29px; color: var(--sky);
    white-space: nowrap;
  }
  .brand-tagline {
    position: absolute; left: 30px; top: 332px;
    font-family: "Didact Gothic", sans-serif;
    font-size: 19px; color: var(--white);
    white-space: nowrap;
  }
  .details-panel { position: relative; flex: 1; }
  .person {
    position: absolute; right: 60px; top: 95px;
  }
  .person-name {
    font-family: "Montserrat", sans-serif; font-weight: 700;
    font-size: 34px; color: var(--navy); line-height: 1.1;
  }
  .person-title {
    font-family: "Didact Gothic", sans-serif;
    font-size: 19px; color: var(--ink-grey); margin-top: 4px;
  }
  .contact-list {
    position: absolute; left: 40px; bottom: 70px;
    list-style: none;
    font-family: "Didact Gothic", sans-serif;
    font-size: 21px; color: var(--ink-grey); line-height: 1.4;
  }
  .contact-label {
    display: inline-block; width: 26px;
    font-family: "Montserrat", sans-serif; font-weight: 700;
    color: var(--ink-grey);
  }
</style>
</head>
<body>
  <main class="canvas">
    <section class="card card--back" aria-label="Card reverse">
      <div class="back-band">
        <span class="back-wordmark">TelmaNord Partners.com.au</span>
      </div>
    </section>

    <section class="card card--front" aria-label="Card front">
      <div class="brand-panel">
        <svg class="brand-mark" viewBox="0 0 190 190" aria-hidden="true">
          <circle cx="95" cy="95" r="90" fill="var(--sky)"/>
        </svg>
        <p class="brand-name">TelmaNord Partners.com.au</p>
        <p class="brand-tagline">Steady Ledger Answers... that deliver</p>
      </div>
      <div class="details-panel">
        <div class="person">
          <h1 class="person-name">Doug Hallett</h1>
          <p class="person-title">Principal</p>
        </div>
        <ul class="contact-list">
          <li><span class="contact-label">P</span>: 1800 493 518</li>
          <li><span class="contact-label">M</span>: 0412 658 071</li>
          <li><span class="contact-label">E</span>: admin@telmanordpartners.com.au</li>
        </ul>
      </div>
    </section>
  </main>
</body>
</html>
```